Thoroughbred Racing Partnership needs web design

Glimmer of Laurel Partners is a management group who buys horses and races them on both the West and East coasts. The premise of the business is for an investment as little as $500, anyone can be a partner and own a percentage of a horse(s). This is a low cost way of getting involved in the exciting sport of Thoroughbred Racing, without shouldering the heavy financial responsibility. Our target market is mostly males 40+ but we want to include all target markets. We are looking for something very clean and professional, we want to give an image of success. Nothing overly "artsy." I have included the logo in which you can incorporate in the site. Also, the logo colors will be the colors of our "silks." The silks are what the jockey wears and will be an important marketing tool for GOL. We would like a very prominent picture of a racehorse somewhere on the homepage, we want to make it clear that is a website for Horseracing partnerships.

On the top of the site, it should say "Glimmer of Laurel" (on the top)
and below that "Thoroughbred Racing Partnerships." (below that)

The main sections, which should be across the top are:

Home
About Us
Ownership
Stable Roster
News
Contact us

Some of these will have drop down menus.

An example of a competitor website that we like is: www.harrowgatefarm.example
An example of a competitor website that we don't like is: www.paddockvue.example
Updates

Project Deadline Extended
Reason: We have a Board of Directors meeting on the 22nd and we will be making a decision on that day. I'm giving an extension so that all designers are able to submit their designs by the 22nd. Thank you!

Target Market(s)

40+ males

Industry/Entity Type

Business

Requirements
Must have
• our logo must be on the site. We would like at least one bold image of a thoroughbred horse in action. The picture is going to tell the story so it needs to be very eye-catching.

Our slogan should also be included on the website, "Experience the thrill of owning a Racehorse."
Should not have
• cartoons, artsy pictures, pictures of Steeplechase horses or "jumpers." This partnership is for racehorses only, there is not jumping involved with the horses.

```html
<!DOCTYPE html>
<html lang="en">
<head>
<meta charset="utf-8">
<title>Glimmer of Laurel Partners</title>
<link href="https://fonts.googleapis.com/css2?family=Oswald:wght@300;400&family=Open+Sans:ital,wght@0,400;0,600;0,700;1,400&display=swap" rel="stylesheet">
<style>
:root{
  --blue:#125189;
  --blue-dark:#0b3d6b;
  --navy:#0a1a57;
  --footer:#071828;
  --footer-line:#1e4460;
  --link:#3fa3e0;
  --grey-bg:#e6e6e6;
  --text:#333;
  --accent:#1a5d94;
}
*{box-sizing:border-box;margin:0;padding:0}
html,body{width:1059px;height:1200px;overflow:hidden}
body{position:relative;font-family:"Open Sans",sans-serif;background:var(--grey-bg);color:var(--text)}
.abs{position:absolute}

.site-header{position:absolute;left:0;top:0;width:1059px;height:103px;background:var(--blue)}
.brand{position:absolute;left:124px;top:4px;width:199px;height:108px;background:#fff;border-radius:30px 30px 0 0 / 10px 10px 0 0;display:flex;align-items:center;justify-content:center;gap:8px;z-index:3;box-shadow:0 2px 4px rgba(0,0,0,.2)}
.brand-dot{width:14px;height:14px;border-radius:50%;background:var(--blue-dark)}
.brand-name{font-family:"Open Sans",sans-serif;font-weight:700;font-size:21px;color:var(--blue-dark);letter-spacing:.5px;white-space:nowrap}
.tagline{position:absolute;left:687px;top:8px;font-style:italic;color:#dce8f3;font-size:15px;line-height:22px}
.main-nav{position:absolute;left:398px;top:69px;display:flex;align-items:center}
.main-nav a{color:#fff;text-decoration:none;font-weight:700;font-size:12px;letter-spacing:.2px;padding:0 13px;line-height:22px;border-left:1px solid #2d6aa0}
.main-nav a:first-child{border-left:0}
.main-nav a.active{background:linear-gradient(#f7fbff,#c5dcef);color:#0b3560;border-radius:3px;padding:0 8px;margin-right:6px}

.hero{position:absolute;left:0;top:103px;width:1059px;height:457px;background:radial-gradient(ellipse at 45% 55%,#6c7a72 0%,#9fb8a8 30%,#bfd0c4 55%,#d7e0dc 80%,#c9d0d0 100%)}
.hero-slogan{position:absolute;left:640px;top:50px;font-family:"Oswald",sans-serif;font-weight:300;font-size:33px;line-height:35px;color:#fff}
.hero-dots{position:absolute;left:816px;top:430px;display:flex;gap:4px}
.hero-dots span{width:31px;height:7px;background:var(--blue-dark)}
.hero-dots span.on{background:#fff}

.intro{position:absolute;left:0;top:560px;width:1059px;height:194px;background:var(--blue)}
.intro h1{position:absolute;left:126px;top:12px;width:526px;font-family:"Oswald",sans-serif;font-weight:400;font-size:23px;color:#fff;padding-bottom:4px;border-bottom:1px solid #4a7fad}
.intro p{position:absolute;left:126px;top:62px;width:540px;font-size:11.7px;font-weight:600;line-height:18.5px;color:#fff}
.btn{position:absolute;font-family:Arial,sans-serif;font-weight:700;font-size:10.5px;text-align:center;border-radius:3px}
.btn-light{background:linear-gradient(#fff,#d9e8f5);color:#13508a}
.btn-blue{background:var(--blue);color:#fff}
.video{position:absolute;left:683px;top:12px;width:250px;height:170px;border:1px solid #fff;background:#1a1a1a;overflow:hidden}
.video-still{position:absolute;left:0;top:0;width:248px;height:143px;background:linear-gradient(135deg,#2b2420,#7a5c4c 45%,#3b3532)}
.video-bar{position:absolute;left:0;bottom:0;width:248px;height:25px;background:linear-gradient(#3a3a3a,#151515);color:#ddd;font-size:8px;display:flex;align-items:center}

.panel{position:absolute;top:778px;width:265px;height:245px;background:linear-gradient(#f4f4f4,#d9d9d9);border-radius:0 0 6px 6px;box-shadow:0 3px 4px rgba(0,0,0,.15)}
.panel-head{height:33px;background:var(--navy);display:flex;align-items:center}
.panel-icon{width:38px;height:38px;border-radius:50%;background:#fff;margin:0 12px 0 5px;display:flex;align-items:center;justify-content:center}
.panel-head h2{font-family:"Oswald",sans-serif;font-weight:400;font-size:21px;color:#fff}
.panel-body{position:relative;padding:8px 9px;font-size:10px;line-height:16.3px;color:#444}
.ticks{list-style:none;margin-top:6px}
.ticks li{color:var(--accent);font-weight:600;font-size:10.5px;line-height:18.5px;padding-left:24px;position:relative}
.ticks svg{position:absolute;left:2px;top:4px}
.field{position:absolute;left:9px;width:239px;height:22px;background:#fbfbf8;border:1px solid #ccc;border-radius:2px;font-size:10px;color:#555;padding:4px 8px}

.quote{position:absolute;left:94px;top:58px;width:166px;font-size:9.6px;line-height:17.3px;color:#444}
.quote-name{position:absolute;left:94px;top:150px;font-size:11.5px;font-weight:600;color:var(--accent);white-space:nowrap}
.quote-role{position:absolute;left:94px;top:171px;font-size:11.5px;font-weight:600;color:#444}

.site-footer{position:absolute;left:0;top:1046px;width:1059px;height:154px;background:var(--footer);color:#fff}
.fcol{position:absolute;top:14px}
.fcol h3{font-weight:600;font-size:13.5px;color:var(--link);padding-bottom:2px;border-bottom:1px dashed #3c5a70}
.vsep{position:absolute;top:6px;width:1px;height:142px;background:var(--footer-line)}
.flinks{list-style:none;margin:10px 0 0 8px;font-size:10.5px;line-height:15px}
.flinks li.on{color:var(--link)}
.footer-brand{position:absolute;left:775px;top:28px;width:150px;text-align:center;font-weight:700;font-size:17px;color:#fff;line-height:24px;white-space:nowrap}
.socials{display:flex;gap:9px}
.socials span{width:25px;height:25px;border-radius:50%;background:#1a66a8}
</style>
</head>
<body>

<header class="site-header">
  <div class="brand"><span class="brand-dot"></span><span class="brand-name">GOL PARTNERS</span></div>
  <div class="tagline">Glimmer of Laurel<br>Thoroughbred Racing Partnerships.</div>
  <nav class="main-nav">
    <a class="active" href="#">HOME</a><a href="#">ABOUT US</a><a href="#">OWNERSHIP</a><a href="#">STABLE ROSTER</a><a href="#">NEWS</a><a href="#">CONTACT US</a>
  </nav>
</header>

<section class="hero" role="img" aria-label="Photograph of a jockey in blue silks celebrating on a grey thoroughbred racehorse on the turf">
  <div class="hero-slogan">Experience the thrill of<br>owning a Racehorse</div>
  <div class="hero-dots"><span class="on"></span><span></span><span></span></div>
</section>

<section class="intro">
  <h1>Glimmer of Laurel Thoroughbred Partnerships</h1>
  <p>Glimmer of Laurel Partners is a management group who buys horses and races them on both the West and East coasts. The premise of the business is for an investment as little as $500, anyone can be a partner and own a percentage of a horse(s). This is a low cost way of getting involved in the exciting sport of Thoroughbred Racing, without shouldering the heavy financial responsibility.</p>
  <div class="btn btn-light" style="left:566px;top:151px;width:79px;height:20px;line-height:20px">Read more »</div>
  <div class="video">
    <div class="video-still" role="img" aria-label="Video still of three men presenting a plaque"></div>
    <svg class="abs" style="left:103px;top:50px" width="40" height="40" viewBox="0 0 40 40"><rect width="40" height="40" rx="4" fill="#c8201e"/><path d="M14 10 L30 20 L14 30Z" fill="#fff"/></svg>
    <div class="video-bar">
      <svg width="20" height="12" style="margin-left:8px"><rect x="5" y="2" width="3" height="9" fill="#bbb"/><rect x="11" y="2" width="3" height="9" fill="#bbb"/></svg>
      <svg width="22" height="12" style="margin-left:8px"><path d="M3 4h3l4-3v10l-4-3H3z" fill="#bbb"/></svg>
      <span style="margin-left:8px">0:00 / 0:00</span>
    </div>
  </div>
</section>

<article class="panel" style="left:124px">
  <div class="panel-head"><div class="panel-icon"><span style="width:20px;height:20px;border-radius:50%;background:var(--blue)"></span></div><h2>Ownership Pride</h2></div>
  <div class="panel-body">
    <p>Lorem ipsum dolor sit amet, consectet adipiscing elit, sed diam nonummy nibh euismod tincidunt ut laoreet dolore magna aliquam erat volutpat.Ut wisi enim ad minim veniam, quis nostru exe ullamcorper suscipit lobortis nisl ut aliquip commod consequat.</p>
    <ul class="ticks">
      <li><svg width="14" height="12"><path d="M1 7l4 4 8-10" stroke="#1a5d94" stroke-width="1.5" fill="none"/></svg>Lorem ipsum dolor sit amet</li>
      <li><svg width="14" height="12"><path d="M1 7l4 4 8-10" stroke="#1a5d94" stroke-width="1.5" fill="none"/></svg>Sed diam nonummy nibh euismod</li>
      <li><svg width="14" height="12"><path d="M1 7l4 4 8-10" stroke="#1a5d94" stroke-width="1.5" fill="none"/></svg>Ut wisi enim ad minim</li>
      <li><svg width="14" height="12"><path d="M1 7l4 4 8-10" stroke="#1a5d94" stroke-width="1.5" fill="none"/></svg>Consectet adipiscing elit</li>
    </ul>
  </div>
  <div class="btn btn-blue" style="left:169px;top:216px;width:79px;height:20px;line-height:20px">Read more »</div>
</article>

<article class="panel" style="left:397px">
  <div class="panel-head"><div class="panel-icon"><svg width="24" height="22" viewBox="0 0 24 22"><path d="M2 3h13v9H8l-4 3v-3H2z" fill="#0b3d6b"/><path d="M17 7h5v9h-2v3l-4-3h-6v-2h7z" fill="#0b3d6b"/></svg></div><h2>Client Testimonials</h2></div>
  <div class="abs" style="left:12px;top:55px;width:66px;height:70px;border:2px solid #fff;background:linear-gradient(#9fb4c8,#56708a)" role="img" aria-label="Portrait photo of a client"></div>
  <p class="quote"><span style="color:#aaa;font-size:13px;line-height:10px">“</span>Ut wisi enim ad mini veniam, quis nostrud exerci tationullamo corper suscipit lobortis nislutalil uip ullamcorper suscipit lobortis aliquip commod consequat.</p>
  <p class="quote-name">Mr. Lorem ipsum sit amet</p>
  <p class="quote-role">Chief Executive</p>
  <div class="btn btn-blue" style="left:171px;top:218px;width:79px;height:20px;line-height:20px">Read more »</div>
</article>

<article class="panel" style="left:670px">
  <div class="panel-head"><div class="panel-icon"><svg width="18" height="22" viewBox="0 0 18 22"><path d="M1 1h11l5 5v15H1z" fill="none" stroke="#0b3d6b" stroke-width="2"/><path d="M5 16l7-8 2 2-7 8H5z" fill="#0b3d6b"/></svg></div><h2>Quick Contact</h2></div>
  <div class="field" style="top:49px">Your Name</div>
  <div class="field" style="top:77px">Email</div>
  <div class="field" style="top:106px">Phone</div>
  <div class="field" style="top:136px;height:63px">Message</div>
  <div class="btn btn-blue" style="left:169px;top:216px;width:79px;height:20px;line-height:20px">Submit</div>
</article>

<footer class="site-footer">
  <div class="fcol" style="left:126px;width:99px">
    <h3>Quick Links</h3>
    <ul class="flinks"><li class="on">Home</li><li>About Us</li><li>Ownership</li><li>Stable Roster</li><li>News</li><li>Contact us</li></ul>
  </div>
  <div class="vsep" style="left:264px"></div>
  <div class="fcol" style="left:301px;width:166px">
    <h3>Newsletter Signup</h3>
    <p style="font-size:10px;line-height:12px;margin:10px 0 0 3px">Signup with us and get news and update in your inbox</p>
    <div style="margin:11px 0 0 1px;width:147px;height:22px;background:#0e2d48;border:1px solid #24506f;font-size:9px;font-style:italic;color:#8aa4b8;padding:4px 5px">Email here</div>
    <div style="margin:10px 0 0 76px;width:72px;height:20px;background:linear-gradient(#fff,#c9d5de);color:#0b2a45;font-size:11.5px;font-weight:600;text-align:center;line-height:20px;border-radius:2px">Signup</div>
  </div>
  <div class="vsep" style="left:505px"></div>
  <div class="fcol" style="left:544px;width:165px">
    <h3>Company Headquarter</h3>
    <p style="font-size:10px;line-height:16px;margin:8px 0 0 3px">Lorem ipsum dolor sit amet<br>consectetuer adipsi<br>Po Box-0050</p>
    <p style="font-size:10.5px;font-weight:600;margin:5px 0 0 3px;display:flex;align-items:center;gap:7px"><svg width="12" height="12" viewBox="0 0 12 12"><path d="M2 1l3 0 1 3-2 1c1 2 2 3 3 3l1-2 3 1v3c-6 0-10-4-9-9z" fill="#8fbfe6"/></svg>001 5550-12345</p>
    <p style="font-size:10.5px;font-weight:600;margin:8px 0 0 3px;display:flex;align-items:center;gap:7px;white-space:nowrap"><svg width="14" height="10" viewBox="0 0 14 10"><rect x=".5" y=".5" width="13" height="9" fill="none" stroke="#8fbfe6"/><path d="M1 1l6 5 6-5" stroke="#8fbfe6" fill="none"/></svg>info@golpartners.example</p>
  </div>
  <div class="vsep" style="left:746px"></div>
  <div class="footer-brand">GOL PARTNERS</div>
  <div class="abs socials" style="left:788px;top:86px"><span></span><span></span><span></span><span></span></div>
  <div class="abs" style="left:786px;top:122px;font-size:8px;color:#ddd;white-space:nowrap">© 2013 Glimmer of Laurel Partners</div>
</footer>

</body>
</html>
```